Corvanth Veylor - Advanced Skincare and undetectable Makeup for Men

We are in need of a professional webpage for our company Corvanth Veylor. We help every man feel his best by looking his best. Inspired by the myth of Corvanth, we offer makeup and skincare products along with education upon their use. Our mission is to celebrate masculinity in all of its forms, regardless of age, race, sexual orientation, or assigned gender at birth.

The webpage would serve as our online store, as a place where our clients can learn about our brand, view our "How-to" video tutorials, and get product information. An online blog will also be hosted in order to keep clients up to date with news, updates, media mentions, etc.

The color schemes that we use are mostly Black and Gold, with Red accents. please keep in mind that this is a men's cosmetics line, and therefore should read powerful, sexy, confident and bold - all with a high end look and feel.

Think along the lines of brands like Lem Brisko, QDV, Belluti, etc.

our logo is included in the files attached. images and copy will be added in at a later time; hence, general images that fit the feel and filler text is encouraged.

The products to be sold include:
a face cleanser in a pump dispenser bottle (1 size)
a mask in a round jar container (1 size)
a moisturizer in a pump container 1 size)
a concealer in a click pen with a brush applicator (3 shades)
a liquid liner pen (4 shades)
a contouring palette (2 shade options)
a setting spray (single option)

Target Market(s)

Millennial Men

Industry/Entity Type

Beauty

Number of Pages Required

5+ page

Font styles to use
Serif

Colors
ec1f27
000000
faa54b

Requirements
Must have
• ur essential requirements are:
• 1) a stunning and engaging landing page that truly captures the ideals of sexuality, boldness and confidence.
• 2) an interactive and engaging online store that is easy to update / add product / information to.
• 3) Product pages supporting various toggling images of the product, a shade selection option, ingredient information, usage instructions, pricing, and a link to a "how to video" unique to each individual product.
• 4) dedicated space where all of the tutorials can be organized together
• 5) an organized Blog section, that would include a segment for a Q&A section for us to update as the brand grows, ongoing contests (that would be easily hidden if there are no contests running at the moment) as well as general news and updates segment.
• 6) an "about us" page, where our customers are able to learn about our story, inspirations, humanitarian efforts and philosophies in product contents and purity.
• 7) a contact us page, which would include social media links, contact email and telephone number as well as physical address to be updated upon launch.
• 8) discrete privacy policy, terms of use, and return policy links available at the bottom of every page
Nice to have
• 1) A posting forum where clients could post their looks using our products, or maybe a live stream of our Pictoval account.
• 2) a member sign in page so that we can collect and store customer information for faster check out, keep track of purchases attached to their email address (future loyalty program plans) and maintain an email database for email notifications and the such.

```html
<!DOCTYPE html>
<html lang="en">
<head>
<meta charset="utf-8">
<title>Corvanth Veylor</title>
<link href="https://fonts.googleapis.com/css2?family=Cinzel:wght@400;500&family=Roboto:ital,wght@0,400;0,500;0,700;1,400;1,500&display=swap" rel="stylesheet">
<style>
:root{
  --gold:#e0a31c;
  --gold-soft:#faa54b;
  --red:#ec1f27;
  --black:#000;
  --ink:#111;
  --dark:#1b1b1b;
  --light:#efefef;
  --text:#666;
  --white:#fff;
}
*{margin:0;padding:0;box-sizing:border-box}
html,body{width:1200px;height:2560px;overflow:hidden}
body{position:relative;font-family:'Roboto',sans-serif;background:var(--black);color:var(--white)}
a{color:inherit;text-decoration:none}
.abs{position:absolute}
svg.ico{display:inline-block;vertical-align:middle}

/* top bar */
.topbar{left:0;top:0;width:1200px;height:38px;background:var(--gold);font-size:13.5px;display:flex;align-items:center;justify-content:space-between;padding:0 99px}
.topbar span.sep{margin:0 14px}
.topbar .account{display:flex;align-items:center;gap:8px}

/* hero */
.hero-photo{left:0;top:38px;width:1200px;height:620px;
  background:
    radial-gradient(ellipse 170px 140px at 640px 380px,rgba(255,214,120,.85),rgba(230,160,60,.45) 45%,rgba(0,0,0,0) 100%),
    radial-gradient(ellipse 340px 380px at 330px 300px,#d7a27a 0%,#b97a52 28%,#7a4628 55%,rgba(30,15,8,0) 100%),
    radial-gradient(ellipse 300px 220px at 880px 210px,rgba(200,140,40,.35),rgba(0,0,0,0) 100%),
    linear-gradient(90deg,#1a0d07 0%,#120906 45%,#060403 100%)}
.logo{left:78px;top:58px;width:200px;text-align:center}
.logo .mark{width:34px;height:34px;border:2px solid var(--gold);margin:0 auto 12px}
.logo .name{font-family:'Cinzel',serif;color:var(--gold);font-size:12.5px;letter-spacing:2px;white-space:nowrap}
.nav{top:86px;left:519px;display:flex;gap:33px;font-size:15px;font-weight:500;align-items:center}
.hero-copy{left:642px;top:232px;width:520px}
.hero-copy h1{font-family:'Cinzel',serif;font-weight:400;font-size:39px;letter-spacing:2px;line-height:1;white-space:nowrap}
.hero-copy p{margin-top:24px;width:470px;font-size:16.5px;line-height:27px;font-weight:500}
.btn-ghost{display:inline-flex;align-items:center;gap:8px;margin-top:20px;border:2px solid var(--white);padding:0 24px;height:46px;font-size:16px;font-weight:700}
.hero-chevron{left:0;top:540px;width:1200px;height:120px}

/* about */
.about{left:0;top:654px;width:1200px;height:464px;background:var(--light)}
.about h2{position:absolute;left:99px;top:70px;font-family:'Cinzel',serif;font-weight:400;font-size:34px;letter-spacing:3px;color:var(--ink);white-space:nowrap}
.about p{position:absolute;left:99px;top:142px;width:533px;font-size:13px;line-height:23px;color:var(--text)}
.btn-red{position:absolute;left:99px;top:304px;width:160px;height:44px;background:var(--red);display:flex;align-items:center;justify-content:center;gap:6px;font-size:15px;font-weight:700}
.video{position:absolute;left:688px;top:82px;width:413px;height:266px;background:linear-gradient(120deg,#7a5a4a,#b89580 45%,#d9c3b2 75%,#8a7060)}
.video .play{position:absolute;left:50%;top:50%;transform:translate(-50%,-50%)}

/* categories */
.categories{left:0;top:1118px;width:1200px;height:295px;display:flex}
.cat{position:relative;width:400px;height:295px}
.cat.skin{background:linear-gradient(135deg,#a58a75,#d6c2b4 50%,#8d7666)}
.cat.makeup{background:linear-gradient(135deg,#bfa895,#e3d4c6 50%,#9e8877)}
.cat.tutorials{background:linear-gradient(135deg,#8f7566,#c8b1a2 55%,#6e5a4f)}
.cat .label{position:absolute}
.cat h3{font-family:'Cinzel',serif;font-weight:500;font-size:28px;letter-spacing:3px;white-space:nowrap}
.cat .more{margin-top:8px;font-size:14px;font-weight:700;display:flex;align-items:center;gap:6px}

/* blog */
.blog{left:0;top:1413px;width:1200px;height:752px;background:radial-gradient(ellipse at 50% 30%,#2a2a2a,#141414 70%)}
.blog h2{position:absolute;top:96px;width:1200px;text-align:center;font-family:'Cinzel',serif;font-weight:400;font-size:37px;letter-spacing:3px}
.card{position:absolute;top:193px;width:307px;height:376px;background:var(--white);border:3px solid var(--white);color:var(--ink)}
.card .photo{height:201px;position:relative}
.card .date{position:absolute;left:0;bottom:0;width:46px;height:62px;color:var(--white);text-align:center;font-family:'Cinzel',serif;padding-top:8px}
.card .date b{display:block;font-size:22px;font-weight:500}
.card .date small{font-size:13px}
.card h4{margin:28px 0 0 20px;font-size:17px;font-weight:500}
.card p{margin:18px 20px 0;font-size:12.5px;line-height:22px;color:var(--text)}
.card .meta{position:absolute;left:20px;right:20px;bottom:14px;border-top:1px solid #e4e4e4;padding-top:14px;font-size:11px;color:#555;display:flex;align-items:center;gap:6px}
.card .meta .more{margin-left:auto;color:var(--red);font-style:italic;font-size:13px;font-weight:500}
.newsletter{position:absolute;top:655px;width:1200px;text-align:center;font-family:'Cinzel',serif;font-size:19px;letter-spacing:2px}

/* footer */
.signup{left:307px;top:2137px;width:586px;height:55px;border:1px solid var(--red);border-radius:28px;background:var(--black);display:flex;align-items:center;z-index:2}
.signup .field{flex:1;padding-left:26px;font-size:14px;font-style:italic;color:#ddd}
.signup .submit{width:170px;height:55px;margin-right:-1px;background:var(--red);border-radius:28px;display:flex;align-items:center;justify-content:center;font-weight:700;font-size:16px}
.footer{left:0;top:2165px;width:1200px;height:327px;background:#0b0b0b;border-top:2px solid var(--red)}
.fcol{position:absolute;top:92px}
.fcol h5{font-size:16px;font-weight:700;margin-bottom:20px}
.fcol li{list-style:none;font-size:13.5px;line-height:24px;display:flex;gap:18px}
.fcol li::before{content:"»";font-size:13px}
.copyright{left:0;top:2492px;width:1200px;height:68px;background:var(--gold);display:flex;align-items:center;justify-content:center;font-size:14px;font-weight:500}
</style>
</head>
<body>

<div class="abs topbar">
  <div>Complimentary Shipping &amp; Returns<span class="sep">|</span>Store Location</div>
  <div class="account">
    <svg class="ico" width="11" height="12" viewBox="0 0 11 12"><rect x="1" y="5" width="9" height="7" fill="#fff"/><path d="M3 5V3.5a2.5 2.5 0 0 1 5 0V5" stroke="#fff" stroke-width="1.5" fill="none"/></svg>Log In<span class="sep">|</span>
    <svg class="ico" width="11" height="12" viewBox="0 0 11 12"><circle cx="5.5" cy="3.5" r="3" fill="#fff"/><path d="M0 12a5.5 5 0 0 1 11 0z" fill="#fff"/></svg>Register<span class="sep">|</span>
    <svg class="ico" width="14" height="12" viewBox="0 0 14 12"><path d="M0 1h3l2 7h7l2-5H4" stroke="#fff" stroke-width="1.5" fill="none"/><circle cx="6" cy="10.5" r="1.3" fill="#fff"/><circle cx="11" cy="10.5" r="1.3" fill="#fff"/></svg>My Cart
  </div>
</div>

<div class="abs hero-photo" role="img" aria-label="Hero photograph: model in warm golden light blowing glowing sparkles from her open hand against a dark background"></div>

<div class="abs logo"><div class="mark"></div><div class="name">CORVANTH VEYLOR</div></div>

<nav class="abs nav">
  <a>HOME</a><a>ABOUT</a><a>PRODUCTS</a><a>HOW TO USE</a><a>BLOG</a><a>CONTACT</a>
  <svg class="ico" width="14" height="14" viewBox="0 0 14 14"><circle cx="5.5" cy="5.5" r="4.3" stroke="#fff" stroke-width="2" fill="none"/><path d="M8.7 8.7L13 13" stroke="#fff" stroke-width="2.4"/></svg>
</nav>

<div class="abs hero-copy">
  <h1>CORVANTH VEYLOR</h1>
  <p>At vero eos et accusamus et iusto dignissimos ducimus qui blanditiis praesentium voluptatum deleniti</p>
  <a class="btn-ghost">READ MORE
    <svg class="ico" width="15" height="15" viewBox="0 0 16 16"><circle cx="8" cy="8" r="8" fill="#fff"/><path d="M5 8h6M8 5l3 3-3 3" stroke="#000" stroke-width="2" fill="none"/></svg></a>
</div>

<section class="abs about">
  <h2>ABOUT CORVANTH VEYLOR</h2>
  <p>At vero eos et accusamus et iusto odio dignissimos ducimus qui blanditiis praesentium voluptatum deleniti atque corrupti quos dolores et quas molestias excepturi sint occaecati cupiditate non provident, similique sunt in culpa qui officia deserunt mollitia animi, id est laborum et dolorum fuga. Et harum quidem rerum facilis est et expedita distinctio. Nam libero tempore, cum soluta nobis est elig cumque nihuo minus id quod maxime...</p>
  <a class="btn-red">READ MORE
    <svg class="ico" width="14" height="14" viewBox="0 0 16 16"><circle cx="8" cy="8" r="8" fill="#fff"/><path d="M5 8h6M8 5l3 3-3 3" stroke="#ec1f27" stroke-width="2" fill="none"/></svg></a>
  <div class="video" role="img" aria-label="Video still: makeup artist applying product to a client's face">
    <svg class="play" width="54" height="54" viewBox="0 0 54 54"><circle cx="27" cy="27" r="27" fill="#ec1f27"/><path d="M21 17l18 10-18 10z" fill="#fff"/></svg>
  </div>
</section>

<svg class="abs hero-chevron" viewBox="0 0 1200 120" preserveAspectRatio="none">
  <polygon points="0,0 598,112 1200,0 1200,120 0,120" fill="#efefef"/>
  <polygon points="0,0 598,104 1200,0 1200,8 598,114 0,8" fill="#e0a31c"/>
</svg>

<section class="abs categories">
  <div class="cat skin" role="img" aria-label="Photograph: woman applying skin care cream in a mirror">
    <div class="label" style="left:55px;top:193px"><h3>SKIN CARE</h3><div class="more">VIEW ALL <svg class="ico" width="13" height="13" viewBox="0 0 16 16"><circle cx="8" cy="8" r="8" fill="#fff"/><path d="M5 8h6M8 5l3 3-3 3" stroke="#333" stroke-width="2" fill="none"/></svg></div></div>
  </div>
  <div class="cat makeup" role="img" aria-label="Photograph: hand holding a brush over an eyeshadow palette">
    <div class="label" style="left:53px;top:47px"><h3>MAKEUP</h3><div class="more">VIEW ALL <svg class="ico" width="13" height="13" viewBox="0 0 16 16"><circle cx="8" cy="8" r="8" fill="#fff"/><path d="M5 8h6M8 5l3 3-3 3" stroke="#333" stroke-width="2" fill="none"/></svg></div></div>
  </div>
  <div class="cat tutorials" role="img" aria-label="Photograph: eyeliner being applied in a close-up tutorial">
    <div class="label" style="left:60px;top:193px"><h3>TUTORIALS</h3><div class="more">WATCH NOW <svg class="ico" width="13" height="13" viewBox="0 0 16 16"><circle cx="8" cy="8" r="8" fill="#fff"/><path d="M5 8h6M8 5l3 3-3 3" stroke="#333" stroke-width="2" fill="none"/></svg></div></div>
  </div>
</section>

<section class="abs blog">
  <h2>LATEST BLOG POST</h2>

  <article class="card" style="left:101px">
    <div class="photo" role="img" aria-label="Photograph: model applying mascara with red lips" style="background:linear-gradient(120deg,#1a1a1a,#5a3a30 50%,#c9a08a)">
      <div class="date" style="background:var(--gold)"><b>11</b><small>JUL</small></div>
    </div>
    <h4>Shrinking From Toil and Pain</h4>
    <p>Dignissimos et ducimus atque qui blanditiis praesentium voluptatum deleniti et quas.</p>
    <div class="meta"><span style="color:var(--gold)">●</span>Dara Wilmot &nbsp;| &nbsp;<span style="color:var(--gold)">◌</span>0 Comments<span class="more">More »</span></div>
  </article>

  <article class="card" style="left:446px">
    <div class="photo" role="img" aria-label="Photograph: woman at a vanity table with makeup brushes" style="background:linear-gradient(180deg,#e6e6e6,#bdb6b0 60%,#7b6a60)">
      <div class="date" style="background:var(--red)"><b>05</b><small>JUL</small></div>
    </div>
    <h4>Expound The Actual Teachings</h4>
    <p>Dignissimos et ducimus atque qui blanditiis praesentium voluptatum deleniti et quas.</p>
    <div class="meta"><span style="color:var(--gold)">●</span>Dara Wilmot &nbsp;| &nbsp;<span style="color:var(--gold)">◌</span>0 Comments<span class="more">More »</span></div>
  </article>

  <article class="card" style="left:792px">
    <div class="photo" role="img" aria-label="Photograph: friends wearing white face masks" style="background:linear-gradient(120deg,#a89070,#e2dccf 55%,#c7b79e)">
      <div class="date" style="background:var(--gold)"><b>08</b><small>JUL</small></div>
    </div>
    <h4>Great Explorer Of The Truth</h4>
    <p>Dignissimos et ducimus atque qui blanditiis praesentium voluptatum deleniti et quas.</p>
    <div class="meta"><span style="color:var(--gold)">●</span>Dara Wilmot &nbsp;| &nbsp;<span style="color:var(--gold)">◌</span>0 Comments<span class="more">More »</span></div>
  </article>

  <div class="newsletter">SIGN UP TO OUR NEWSLETTER TO STAY UPDATED</div>
</section>

<footer class="abs footer">
  <div class="fcol" style="left:97px"><h5>CUSTOMER CARE</h5><ul><li>Contact Us</li><li>Size Guide</li><li>My Order</li><li>My Account</li><li>Payment</li><li>Authenticity</li></ul></div>
  <div class="fcol" style="left:382px"><h5>SHIPPING &amp; RETURNS</h5><ul><li>Payment</li><li>Save cards</li><li>Shipping</li><li>Return</li><li>Check Out</li></ul></div>
  <div class="fcol" style="left:688px"><h5>COMPANY</h5><ul><li>About Us</li><li>Careers</li><li>Reseller</li><li>Blog Post</li></ul></div>
  <div class="fcol" style="left:901px"><h5>LEGAL AREA</h5><ul><li>Terms and conditions of Sale</li><li>Privacy Policy</li><li>Track your order</li></ul></div>
</footer>

<div class="abs signup"><span class="field">Your Email Address Here...</span><a class="submit">SUBSCRIBE</a></div>

<div class="abs copyright">© Copyright 2018 Corvanth Veylor. All Rights Reserved.</div>

</body>
</html>
```